Thornvale Group needs a business card design

We need a new business card design using the logo recently selected in a logo competition on Pixel Bazaar. Our business is a consultancy specializing in aviation and energy and the winning business card design will promote an image of precision and professionalism with creativity.

Please use the logo with the name on the front of the card and use a complementary font. Make the back white with either the light grey or dark grey logo.

Target Market(s)

Senior finance and legal leaders at aviation and energy companies

Industry/Entity Type

Management Consulting

Contact Information for Business Card

Peter Castrell
President
Thornvale Group

www.thornvalegroup.example

(555) 204-6391
pc@thornvalegroup.example

Requirements
Must have
• Professional font that goes well with the logo font

```html
<!DOCTYPE html>
<html lang="en">
<head>
<meta charset="utf-8">
<title>Thornvale Group – Business Card</title>
<link rel="stylesheet" href="https://fonts.googleapis.com/css2?family=Montserrat:wght@400&family=Open+Sans:wght@400;700&display=swap">
<style>
  :root {
    --navy: #0f3a66;
    --steel: #2f5f86;
    --ink: #1c3a5c;
    --grey: #6b6f74;
    --logo-grey: #55595e;
    --paper: #ffffff;
    --backdrop: #e6e7e9;
  }
  * { box-sizing: border-box; margin: 0; padding: 0; }
  html, body {
    width: 1200px; height: 913px; overflow: hidden;
    background: var(--backdrop);
    font-family: "Open Sans", Arial, sans-serif;
  }
  .canvas { position: relative; width: 1200px; height: 913px; }

  .card {
    position: absolute;
    width: 525px; height: 300px;
    border-radius: 3px;
    overflow: hidden;
    background: var(--paper);
    box-shadow: 0 10px 28px rgba(0,0,0,.18);
  }
  .card--front { left: 60px; top: 150px; }
  .card--back {
    left: 615px; top: 460px;
    display: flex; align-items: center; justify-content: center;
  }

  .brand {
    display: flex; align-items: center; gap: 14px;
    font-family: "Montserrat", Arial, sans-serif;
    font-weight: 400; text-transform: uppercase;
    color: var(--steel);
  }
  .brand__mark { width: 14px; height: 14px; background: currentColor; flex: none; }
  .brand__name { display: flex; flex-direction: column; align-items: flex-end; line-height: 1; }
  .brand__line--main { font-size: 28px; letter-spacing: 5px; }
  .brand__line--sub { font-size: 14px; letter-spacing: 14px; margin-top: 8px; margin-right: -14px; }

  .card--front .brand { position: absolute; right: 34px; top: 30px; }

  .card--back .brand { color: var(--logo-grey); gap: 18px; }
  .card--back .brand__mark { width: 20px; height: 20px; }
  .card--back .brand__line--main { font-size: 34px; letter-spacing: 6px; }
  .card--back .brand__line--sub { font-size: 17px; letter-spacing: 17px; margin-right: -17px; margin-top: 10px; }

  .rule {
    position: absolute; left: 110px; right: 0; top: 152px;
    height: 1px; background: var(--steel);
  }

  .holder { position: absolute; left: 30px; top: 122px; }
  .holder__name { font-weight: 700; font-size: 20px; color: var(--ink); line-height: 1.2; }
  .holder__title { font-size: 13px; color: var(--grey); margin-top: 4px; }

  .contact-band {
    position: absolute; left: 300px; right: 0; top: 172px; bottom: 0;
    background: linear-gradient(180deg, var(--steel) 0%, var(--navy) 100%);
    padding: 20px 18px 0 0;
    display: flex; flex-direction: column; align-items: flex-end; gap: 6px;
  }
  .contact {
    display: flex; align-items: center; gap: 6px;
    color: var(--paper); font-size: 12px; white-space: nowrap;
  }
  .contact svg { width: 11px; height: 11px; fill: none; stroke: var(--paper); stroke-width: 1.6; flex: none; }
</style>
</head>
<body>
<main class="canvas">
  <section class="card card--front" aria-label="Card front">
    <div class="brand">
      <span class="brand__mark"></span>
      <span class="brand__name">
        <span class="brand__line--main">Thornvale</span>
        <span class="brand__line--sub">Group</span>
      </span>
    </div>
    <div class="rule"></div>
    <div class="holder">
      <p class="holder__name">Peter Castrell</p>
      <p class="holder__title">President</p>
    </div>
    <div class="contact-band">
      <p class="contact">(555) 204-6391
        <svg viewBox="0 0 12 12"><path d="M2 1.5l2 0 1 2.5-1.2 1a6 6 0 0 0 3.2 3.2l1-1.2 2.5 1v2a1 1 0 0 1-1 1A9 9 0 0 1 1 2.5a1 1 0 0 1 1-1z"/></svg>
      </p>
      <p class="contact">pc@thornvalegroup.example
        <svg viewBox="0 0 12 12"><rect x="1" y="2.5" width="10" height="7" rx="1"/><path d="M1 3l5 3.5L11 3"/></svg>
      </p>
      <p class="contact">www.thornvalegroup.example
        <svg viewBox="0 0 12 12"><circle cx="6" cy="6" r="5"/><path d="M1 6h10M6 1c2.5 3 2.5 7 0 10M6 1c-2.5 3-2.5 7 0 10"/></svg>
      </p>
    </div>
  </section>

  <section class="card card--back" aria-label="Card back">
    <div class="brand">
      <span class="brand__mark"></span>
      <span class="brand__name">
        <span class="brand__line--main">Thornvale</span>
        <span class="brand__line--sub">Group</span>
      </span>
    </div>
  </section>
</main>
</body>
</html>
```